Logo and Website Design for QR.KA Horizon - a Software Engineering and IT company

Software engineering and IT are two different disciplines - and yet inseparably linked. At QR.KA Horizon, we combine both worlds and ensure that our software solutions are not only innovative and powerful, but also integrate perfectly into existing IT landscapes. Vision stands more for imagination, so it is not neccessary something what has to do with visualisation. Please consider that the winning competitor is also instructed to make a logo for the company. So please make a suitable logo for QR.KA Horizon to which the website fits to and show it during the website creation process. A good Logo desing is important for winning the competition. The website should contain a landing page with inspiring, perhaps futuristic photos of a datacenter and lines of code. Eventuelly flewent integrated in the text. On the landing page the company should introduced with a small text (max 250 words) followed by a section with a short text to one of our products nearby a graphic visualising the architecture of the product. The menue should be on top and fixed during scrolling and consist of the menue items home, solutions, who are we and a contact button. There should be a footer for linking social media, rights and Impressum. Only as an idea not a must. The very first view on the landing page could also be the menue bar and below of it a transparent unsharp photo (e.g. datacenter, lines of code, both ;) with the company name in the center.

###############################################################

Hi Designers,

Despite your very good approaches for describing QR.KA Horizon, here a short introduction (german text) from ourself:

------
QR.KA Horizon – Ihr Partner für ganzheitliche Softwarelösungen

Die QR.KA Horizon ist ein dynamisches Unternehmen, das sich nicht nur auf die Konzeption, das Design und die Entwicklung maßgeschneiderter Software spezialisiert hat, sondern auch deren reibungslosen Betrieb sicherstellt. Mit einem Team aus erfahrenen Softwarearchitekten und IT-Professionals verbinden wir modernste Softwareentwicklung mit tiefgehendem IT-Know-how – für Lösungen, die nachhaltig, leistungsstark und zukunftssicher sind.

Software Engineering trifft IT – Perfektion in Kombination
Software Engineering und IT sind zwei unterschiedliche Disziplinen – und doch untrennbar miteinander verbunden. Wir bei QR.KA Horizon vereinen beide Welten und sorgen dafür, dass unsere Softwarelösungen nicht nur innovativ und leistungsfähig sind, sondern sich auch perfekt in bestehende IT-Landschaften integrieren.

Expertise mit Fokus auf Healthcare & komplexe IT-Umgebungen
Unsere Experten bringen jahrzehntelange Erfahrung aus dem Healthcare-Sektor mit und unterstützen IT-Abteilungen großer Kliniken in der Entwicklung und Optimierung von Softwarelösungen. Von Anwendungssoftware bis hin zu Steuerungssystemen – unsere Softwareingenieure wissen genau, worauf es ankommt.

Ganzheitlicher Ansatz – über die Software hinaus
Wir entwickeln nicht nur Software, sondern übernehmen auch die Verantwortung für deren stabile und effiziente Betriebsumgebung. Egal, ob on-premises, in der Cloud oder als SaaS-Lösung – wir kümmern uns um den kompletten Lifecycle Ihrer Anwendung.

Ihre Vision – unsere Mission.
Ob Neuentwicklung einer SaaS-Anwendung oder die Migration bestehender Lösungen in eine moderne SaaS-Umgebung – mit QR.KA Horizon haben Sie einen starken Partner an Ihrer Seite.

Lassen Sie uns gemeinsam die Zukunft Ihrer Software gestalten!
--------------

Our first solution called "Clear Record Transfer Gateway" (CLURA)
-------------------
Teilen Sie Ihre Daten sicher – ohne Kompromisse!

Sie nutzen eine relationale Datenbank (Brightcask, Tabulon Hub, Vellumdb etc.) und möchten ausgewählte Daten mit Dritten teilen – sei es für ein Data Warehouse, Business Controller, Lieferanten oder Kunden? Doch dabei sollen Datensicherheit, Integrität und Verfügbarkeit Ihrer primären Lösung in keiner Weise gefährdet werden?

Mit unserer Lösung erhalten Sie genau das: Maximalen Schutz für Ihre Anwendung bei gleichzeitigem Nutzen durch autorisierte Dritte – ganz ohne teure Lizenzkosten für eine Schattendatenbank.

Lassen Sie uns gemeinsam herausfinden, wie Sie Ihre Daten sicher und effizient nutzen können. Kontaktieren Sie uns – wir zeigen Ihnen, was möglich ist!
---------------------

Our second solution MIVO:
---------------------
MIVO – Program for a Tone Matching Instrument ist die smarte Lösung für Unternehmen, die bei Farbgenauigkeit keine Kompromisse machen. Die Software erkennt Farbabweichungen zwischen Mustern vollautomatisch, beschreibt sie verständlich und sorgt so für gleichbleibend hohe Produktqualität – schnell, visuell und präzise. Perfekt für alle, die Farbe zur Vertrauenssache machen.
-------------------------

Thanks,
Gerold

Target Market(s)

IT Professionals from any sector

Industry/Entity Type

Healthcare and other

Coding

Coded - Design and coding required

Number of Pages Required

1 page

Font styles to use
Sans Serif

Colors
0054AA
0677BA
7BADD7
CADEEF
E8F1F8
0094D4
00A9DD
6FCCEA
C7EBF8
E9F6FB
00AB8E
00BBA5
67D7C9
C6EFE9
E9F9F6

Requirements
Must have
• Please see description
Nice to have
• On the landing page the company should introduced with a small text (max 250 words) followed by a section with a short text to one of our products nearby a graphic visualising the architecture of the product. The menue should be on top and fixed during scrolling and consist of the menue items home, solutions, who are we and a contact button. There should be a footer for linking social media, rights and Impressum. Only as an idea not a must. The very first view on the landing page could also be the menue bar and below of it a transparent unsharp photo (e.g. datacenter, lines of code, both ;) with the company name in the center.
Should not have
• Please see description

```html
<!DOCTYPE html>
<html lang="de">
<head>
<meta charset="utf-8">
<title>QR.KA Horizon – Software Engineering</title>
<link href="https://fonts.googleapis.com/css2?family=Montserrat:wght@300;400;500;600;700&display=swap" rel="stylesheet">
<style>
:root{
  --blue-deep:#0054AA;
  --blue:#0677BA;
  --blue-bright:#0094D4;
  --cyan:#00A9DD;
  --sky:#7BADD7;
  --pale:#E8F1F8;
  --section-bg:#EDF2F9;
  --teal:#00AB8E;
  --teal-light:#00BBA5;
  --navy:#0A1A4F;
  --navy-dark:#07143F;
  --ink:#111827;
  --text:#3b4150;
  --white:#ffffff;
  --star:#F7941D;
}
*{box-sizing:border-box;margin:0;padding:0}
html,body{width:1200px;height:4093px;overflow:hidden}
body{font-family:"Montserrat",sans-serif;color:var(--ink);background:var(--white);position:relative}
.abs{position:absolute}
.brand{display:flex;align-items:center;gap:8px;font-weight:600;font-size:21px;color:var(--blue-deep);letter-spacing:.2px;white-space:nowrap}
.brand-dot{width:26px;height:26px;border-radius:50%;border:3px solid currentColor}
.divider{width:40px;height:3px;background:var(--teal);border-radius:2px}
.btn{display:flex;align-items:center;justify-content:center;border-radius:20px;font-weight:500;font-size:14px;text-decoration:none;white-space:nowrap}

/* hero */
.hero{position:absolute;left:0;top:0;width:1200px;height:650px;background:linear-gradient(120deg,#0a6fd6 0%,#0054AA 55%,#0a3d8a 100%);overflow:hidden}
.hero-visual{position:absolute;inset:0;clip-path:polygon(750px 0,1200px 0,1200px 650px,865px 650px,530px 330px);background:radial-gradient(circle at 80% 35%,#1b8fe0 0%,#0a3b7d 40%,#061a45 85%)}
.hero-shade{position:absolute;inset:0;clip-path:polygon(750px 0,530px 330px,200px 650px,865px 650px);background:linear-gradient(180deg,rgba(0,60,150,.35),rgba(0,40,110,.55))}
.nav{position:absolute;left:140px;top:38px;width:918px;height:57px;background:var(--white);border-radius:30px;display:flex;align-items:center;padding:0 8px 0 26px}
.nav .brand{font-size:20px}
.nav-links{display:flex;gap:36px;margin-left:auto;margin-right:34px;font-size:13px;font-weight:500;color:var(--ink);white-space:nowrap}
.nav-links span{position:relative}
.nav-links .active::before{content:"";position:absolute;left:50%;top:-22px;width:22px;height:3px;background:var(--blue-bright);transform:translateX(-50%)}
.caret{font-size:8px;margin-left:5px}
.nav-cta{background:var(--blue-deep);color:var(--white);width:204px;height:38px;font-size:14px}
.hero-title{position:absolute;left:140px;top:192px;font-size:45px;line-height:60px;font-weight:700;color:var(--white)}
.hero-lead{position:absolute;left:140px;top:382px;font-size:15px;line-height:27px;color:var(--white);font-weight:500}
.hero-cta{position:absolute;left:140px;top:466px;width:190px;height:38px;background:var(--white);color:var(--blue-deep);font-weight:600}
.explore{position:absolute;left:0;width:1200px;top:585px;text-align:center;color:var(--white);font-size:11px;font-weight:600;letter-spacing:1.5px}

/* about */
.about-img{position:absolute;left:140px;top:742px;width:504px;height:518px;border-radius:260px 260px 260px 260px/300px 240px 280px 250px;background:linear-gradient(150deg,#2a3550 0%,#3c5a86 45%,#a77b4f 80%,#2c3e62 100%);transform:rotate(-8deg)}
.info-icon{position:absolute;left:712px;top:784px;width:38px;height:38px;border-radius:50%;background:var(--teal-light);color:#fff;font-weight:700;display:flex;align-items:center;justify-content:center;font-size:18px}
.about-kicker{position:absolute;left:710px;top:836px;font-size:36px;font-weight:300}
.about-title{position:absolute;left:710px;top:882px;font-size:36px;line-height:50px;font-weight:700;white-space:nowrap}
.about-divider{position:absolute;left:710px;top:988px}
.caps{font-size:12px;font-weight:600;text-transform:uppercase;line-height:24px;white-space:nowrap}
.body{font-size:12.5px;line-height:22.6px;color:var(--text)}

/* solutions */
.solutions{position:absolute;left:0;top:1351px;width:1200px;height:869px;background:var(--section-bg)}
.sec-title{position:absolute;left:0;width:1200px;text-align:center;font-size:36px;font-weight:700}
.sec-sub{position:absolute;left:0;width:1200px;text-align:center;font-size:36px;font-weight:300}
.center-div{position:absolute;left:580px}
.card{position:absolute;left:140px;top:240px;width:918px;height:491px;background:var(--white);box-shadow:0 6px 24px rgba(0,40,100,.08)}
.card-title{position:absolute;left:52px;top:46px;font-size:23px;line-height:41px;font-weight:500;width:390px}
.card-text{position:absolute;left:52px;width:385px;font-size:12px;line-height:22.6px;color:var(--text)}
.card-media{position:absolute;left:459px;top:0;width:459px;height:491px;background:linear-gradient(160deg,#0677BA,#0054AA)}
.card-img{position:absolute;left:30px;top:30px;width:401px;height:434px;background:linear-gradient(180deg,#f3f5f8 0%,#c9d3df 40%,#1c3a5a 60%,#7ab7dd 80%,#e9eef3 100%)}
.dots{position:absolute;left:577px;top:780px;display:flex;gap:6px}
.dots i{width:20px;height:5px;border-radius:3px;background:var(--teal)}
.dots i+i{background:#c6ccd6}

/* industry */
.ind-icon{width:60px;height:60px;border-radius:10px;background:var(--blue-deep);display:flex;align-items:center;justify-content:center}
.ind-icon.teal{background:var(--teal-light)}
.ind-item h3{font-size:16px;font-weight:500;margin-top:26px}
.ind-item p{font-size:12px;line-height:22px;color:var(--text);margin-top:8px;width:220px}

/* cta */
.cta-bg{position:absolute;left:0;top:2924px;width:1200px;height:811px;background:var(--section-bg)}
.cta{position:absolute;left:140px;top:2786px;width:918px;height:284px;border-radius:28px;overflow:hidden;background:linear-gradient(90deg,#1a4b8a 0%,#0d3170 40%,#0a1f5c 65%,#0a1a4f 100%)}
.cta-title{position:absolute;left:504px;top:50px;font-size:32px;line-height:44px;color:#fff;font-weight:700}
.cta-text{position:absolute;left:504px;top:140px;font-size:13px;line-height:22px;color:#fff;width:380px}
.cta-btn{position:absolute;left:504px;top:202px;width:201px;height:35px;background:var(--blue-bright);color:#fff}

/* testimonials */
.avatar{position:absolute;border-radius:50%;background:radial-gradient(circle at 50% 40%,#d9c1a8 0%,#8e7a69 55%,#cfd8e3 100%);border:4px solid #fff;box-shadow:0 0 0 2px #6FCCEA}
.quote{position:absolute;left:420px;top:3540px;width:360px;text-align:center;font-size:12.5px;line-height:22.6px;color:var(--text)}
.quote-name{position:absolute;left:0;width:1200px;top:3651px;text-align:center;font-size:13px;font-weight:600}
.stars{position:absolute;left:0;width:1200px;top:3674px;text-align:center;color:var(--star);font-size:19px;letter-spacing:4px}

/* footer */
.footer{position:absolute;left:0;top:3735px;width:1200px;height:309px;background:var(--navy)}
.footer .brand{color:#fff}
.footer h4{position:absolute;font-size:15px;font-weight:600;color:#fff;padding-bottom:8px;white-space:nowrap}
.footer h4::after{content:"";position:absolute;left:0;bottom:0;width:36px;height:2px;background:var(--teal)}
.ftxt{position:absolute;color:#fff;font-size:12px;line-height:22px}
.links li{list-style:none;font-size:13px;line-height:28.6px;color:#fff}
.links li::before{content:"▸";color:var(--cyan);font-size:10px;margin-right:9px}
.c-row{position:absolute;display:flex;align-items:center;gap:16px;color:#fff;font-size:13px}
.c-ico{width:30px;height:30px;border-radius:50%;background:rgba(255,255,255,.12);display:flex;align-items:center;justify-content:center}
.social{position:absolute;left:140px;top:3955px;display:flex;gap:26px}
.social i{width:16px;height:16px;border-radius:50%;border:2px solid #fff}
.input{position:absolute;left:860px;top:3878px;width:198px;height:39px;border:1px solid rgba(255,255,255,.6);border-radius:20px;color:rgba(255,255,255,.7);font-size:11px;padding:0 20px;display:flex;align-items:center}
.sub-btn{position:absolute;left:860px;top:3938px;width:198px;height:35px;background:var(--blue-bright);color:#fff;font-weight:600}
.bottom{position:absolute;left:0;top:4044px;width:1200px;height:49px;background:var(--navy-dark);color:#fff;font-size:12px}
</style>
</head>
<body>

<header class="hero">
  <div class="hero-shade"></div>
  <div class="hero-visual" role="img" aria-label="Digitaler Datenstrom aus Binärcode, der in ein leuchtendes Netzwerk-Symbol mündet"></div>
  <nav class="nav">
    <div class="brand"><span class="brand-dot"></span>QR.KA Horizon</div>
    <div class="nav-links">
      <span class="active">Heim</span>
      <span>Lösungen<span class="caret">▼</span></span>
      <span>Wer Sind Wir<span class="caret">▼</span></span>
    </div>
    <a class="btn nav-cta">Kontaktieren Sie Uns</a>
  </nav>
  <h1 class="hero-title">Mit Präzision<br>Die Zukunft<br>Vorantreiben</h1>
  <p class="hero-lead">Innovative Lösungen für Leistung,<br>Sicherheit und Skalierbarkeit</p>
  <a class="btn hero-cta">Legen Sie Los</a>
  <div class="explore">ENTDECKEN SIE MEHR
    <svg width="14" height="10" viewBox="0 0 14 10" style="display:block;margin:8px auto 0"><path d="M2 2l5 5 5-5" fill="none" stroke="#fff" stroke-width="2"/></svg>
  </div>
</header>

<section class="about">
  <div class="about-img" role="img" aria-label="Geschäftsmann im Anzug vor digitalen Code-Einblendungen und einem leuchtenden Globus"></div>
  <div class="info-icon">i</div>
  <div class="about-kicker">Über Uns</div>
  <h2 class="about-title">QR.KA Horizon Software<br>Engineering</h2>
  <div class="divider about-divider"></div>
  <div class="abs caps" style="left:710px;top:1012px">Ihr Partner für ganzheitliche Softwarelösungen</div>
  <p class="abs body" style="left:710px;top:1046px;width:380px">QR.KA Horizon ist ein dynamisches Unternehmen, das sich nicht nur auf die Konzeption, das Design und die Entwicklung maßgeschneiderter Software spezialisiert hat, sondern auch deren reibungslosen Betrieb gewährleistet. Mit einem Team aus erfahrenen Softwarearchitekten und IT-Experten verbinden wir modernste Softwareentwicklung mit fundierter IT-Expertise – für nachhaltige, leistungsstarke und zukunftssichere Lösungen.</p>
</section>

<section class="solutions">
  <h2 class="sec-title" style="top:80px">Lösungen, Die Probleme Lösen.</h2>
  <div class="sec-sub" style="top:128px">Skalierbare Systeme</div>
  <div class="divider center-div" style="top:189px"></div>
  <article class="card">
    <h3 class="card-title">01. Clear Record Transfer<br>Gateway (CLURA)</h3>
    <div class="abs caps" style="left:52px;top:137px;font-size:12px">Teilen Sie Ihre Daten sicher – ohne Kompromisse!</div>
    <p class="card-text" style="top:172px">Sie nutzen eine relationale Datenbank (Brightcask, Tabulon Hub, Vellumdb etc.) und möchten ausgewählte Daten mit Dritten teilen – sei es für ein Data Warehouse, einen Business Controller, Lieferanten oder Kunden? Dabei möchten Sie die Datensicherheit, Integrität und Verfügbarkeit Ihrer primären Lösung jedoch in keiner Weise gefährden?</p>
    <p class="card-text" style="top:342px">Mit unserer Lösung erhalten Sie genau das: maximalen Schutz für Ihre Anwendung und gleichzeitig die…</p>
    <a class="btn abs" style="left:52px;top:410px;width:203px;height:37px;background:var(--blue-deep);color:#fff">Erfahren Sie Mehr</a>
    <div class="card-media">
      <div class="card-img" role="img" aria-label="Serverschränke in einem hellen Rechenzentrum mit leuchtendem Schloss für Datenschutz"></div>
    </div>
  </article>
  <div class="dots"><i></i><i></i></div>
</section>

<section class="industry">
  <h2 class="abs" style="left:140px;top:2314px;font-size:36px;line-height:50px;font-weight:700">Industrie Bereit</h2>
  <div class="abs" style="left:140px;top:2364px;font-size:36px;line-height:50px;font-weight:300">Missionsorientiert</div>
  <div class="divider abs" style="left:140px;top:2423px"></div>
  <div class="abs caps" style="left:140px;top:2445px;font-size:12px">Vertrauen von Fachleuten aus den Bereichen<br>Verteidigung, Energie, Logistik &amp; darüber hinaus</div>

  <div class="ind-item abs" style="left:588px;top:2312px">
    <div class="ind-icon"><svg width="28" height="24" viewBox="0 0 28 24" fill="#fff"><circle cx="14" cy="6" r="4"/><circle cx="5" cy="8" r="3"/><circle cx="23" cy="8" r="3"/><path d="M7 22c0-5 3-9 7-9s7 4 7 9z"/><path d="M0 20c0-4 2-7 5-7 1 0 2 .3 3 1-1.5 1.8-2.4 4-2.6 6z"/><path d="M28 20c0-4-2-7-5-7-1 0-2 .3-3 1 1.5 1.8 2.4 4 2.6 6z"/></svg></div>
    <h3>Militär</h3>
    <p>Lorem Ipsum is simply dummy text of the printing and typesetting industry. Lorem Ipsum has.</p>
  </div>
  <div class="ind-item abs" style="left:850px;top:2312px">
    <div class="ind-icon"><svg width="30" height="22" viewBox="0 0 30 22" fill="#fff"><path d="M15 0L0 7l15 7 15-7z"/><path d="M6 11v6c0 2 4 4 9 4s9-2 9-4v-6l-9 4z"/></svg></div>
    <h3>Ingenieurinnen</h3>
    <p>Lorem Ipsum is simply dummy text of the printing and typesetting industry. Lorem Ipsum has.</p>
  </div>
  <div class="ind-item abs" style="left:588px;top:2528px">
    <div class="ind-icon"><svg width="28" height="28" viewBox="0 0 28 28" fill="none" stroke="#fff" stroke-width="2.5"><circle cx="14" cy="14" r="8"/><circle cx="14" cy="14" r="3" fill="#fff"/><path d="M14 0v5M14 23v5M0 14h5M23 14h5"/></svg></div>
    <h3>Techniker</h3>
    <p>Lorem Ipsum is simply dummy text of the printing and typesetting industry. Lorem Ipsum has.</p>
  </div>
  <div class="ind-item abs" style="left:850px;top:2528px">
    <div class="ind-icon teal"><svg width="28" height="24" viewBox="0 0 28 24" fill="#fff"><path d="M10 0h8a2 2 0 012 2v3h-2V2h-8v3H8V2a2 2 0 012-2z"/><rect x="0" y="5" width="28" height="19" rx="3"/><rect x="11" y="11" width="6" height="5" fill="#00BBA5"/></svg></div>
    <h3>Logistikzentren</h3>
    <p>Lorem Ipsum is simply dummy text of the printing and typesetting industry. Lorem Ipsum has.</p>
  </div>
</section>

<div class="cta-bg"></div>
<section class="cta">
  <div class="abs" style="left:0;top:0;width:560px;height:284px;background:linear-gradient(90deg,rgba(200,110,50,.35),rgba(30,90,160,.25) 50%,rgba(10,31,92,0))" role="img" aria-label="Leuchtendes Netzwerk aus Verbindungslinien über der Erde bei Nacht"></div>
  <h2 class="cta-title">Ein Gespräch Entfernt<br>Von Ihrer Lösung</h2>
  <p class="cta-text">Kontaktieren Sie uns noch heute und entdecken Sie, was wir gemeinsam aufbauen können</p>
  <a class="btn cta-btn">Erfahren Sie Mehr</a>
</section>

<section class="testimonials">
  <h2 class="sec-title" style="top:3180px">Vertrauen Von Teams, Die Das</h2>
  <div class="sec-sub" style="top:3230px">Beste Verlangen</div>
  <div class="divider center-div" style="top:3290px"></div>
  <svg class="abs" style="left:0;top:3290px" width="1200" height="340" viewBox="0 3290 1200 340" stroke="#8a97ad" stroke-width="1" fill="none">
    <path d="M302 3325L137 3433L250 3599L302 3325L380 3456L137 3433M380 3456L250 3599M302 3325L621 3445M380 3456L621 3445L825 3340L903 3493L1042 3385L825 3340M903 3493L1022 3572L1042 3385M621 3445L903 3493"/>
  </svg>
  <div class="avatar" role="img" aria-label="Porträtfoto einer Kundin" style="left:269px;top:3292px;width:66px;height:66px"></div>
  <div class="avatar" role="img" aria-label="Porträtfoto eines Kunden" style="left:104px;top:3400px;width:66px;height:66px"></div>
  <div class="avatar" role="img" aria-label="Porträtfoto einer Kundin" style="left:347px;top:3423px;width:66px;height:66px"></div>
  <div class="avatar" role="img" aria-label="Porträtfoto eines Kunden" style="left:217px;top:3566px;width:66px;height:66px"></div>
  <div class="avatar" role="img" aria-label="Porträtfoto der zitierten Kundin" style="left:567px;top:3391px;width:108px;height:108px;border-width:5px;box-shadow:0 0 0 3px #0094D4"></div>
  <div class="avatar" role="img" aria-label="Porträtfoto eines Kunden" style="left:792px;top:3307px;width:66px;height:66px"></div>
  <div class="avatar" role="img" aria-label="Porträtfoto einer Kundin" style="left:1009px;top:3352px;width:66px;height:66px"></div>
  <div class="avatar" role="img" aria-label="Porträtfoto einer Kundin" style="left:870px;top:3460px;width:66px;height:66px"></div>
  <div class="avatar" role="img" aria-label="Porträtfoto eines Kunden" style="left:989px;top:3539px;width:66px;height:66px"></div>
  <p class="quote">“ Lorem Ipsum is simply dummy text of the printing and typesetting industry. Lorem Ipsum has been the industry’s standard dummy text ever since the 1500s, when an unknown printer took a galley of type and scrambled it to make”</p>
  <div class="quote-name">– MARTA L. , CHIEF FINANCE OFFICER</div>
  <div class="stars">★★★★★</div>
</section>

<footer class="footer">
  <div class="brand abs" style="left:140px;top:94px">QR.KA Horizon</div>
  <div class="ftxt" style="left:140px;top:132px">Innovative Software trifft auf<br>echte IT-Expertise</div>

  <h4 style="left:435px;top:93px">Quicklinks</h4>
  <ul class="links abs" style="left:437px;top:136px"><li>Heim</li><li>Lösungen</li><li>Wer Sind Wir</li><li>Kontakt</li></ul>

  <h4 style="left:617px;top:93px">Kontakt Uns</h4>
  <div class="c-row" style="left:617px;top:135px"><span class="c-ico"><svg width="14" height="14" viewBox="0 0 24 24" fill="#fff"><path d="M6.6 10.8a15 15 0 006.6 6.6l2.2-2.2c.3-.3.7-.4 1-.2 1.1.4 2.3.6 3.6.6.6 0 1 .4 1 1V20c0 .6-.4 1-1 1A17 17 0 013 4c0-.6.4-1 1-1h3.5c.6 0 1 .4 1 1 0 1.3.2 2.5.6 3.6.1.3 0 .7-.2 1z"/></svg></span>(555)-204-7781</div>
  <div class="c-row" style="left:617px;top:180px"><span class="c-ico"><svg width="14" height="11" viewBox="0 0 14 11" fill="none" stroke="#fff" stroke-width="1.4"><rect x="1" y="1" width="12" height="9" rx="1"/><path d="M1 1l6 5 6-5"/></svg></span>info@qrka-horizon.example</div>

  <h4 style="left:860px;top:91px">Newsletter Abonnieren</h4>
</footer>
<div class="social"><i></i><i></i><i></i><i></i></div>
<div class="input">Eingeben E-Mail</div>
<a class="btn sub-btn">Jetzt Abonnieren</a>
<div class="bottom">
  <span class="abs" style="left:140px;top:17px">Copyright © 2025 QR.KA Horizon Software Engineering Technology | Alle Rechte Vorbehalten.</span>
  <span class="abs" style="left:990px;top:17px">Impressum</span>
</div>

</body>
</html>
```